Business Card Design Project

This is the first time we use our new logo. We need a business card that we can use both on our institutional corporate relationships and also that works for our staff that deals with consumers directly.

VELUNDA is a new company dedicated to empower consumers and to provide them with the best choices for specialized health care using the latest telemedicine technology (medicine at a distance via videoconference).

We want to print this cards in high quality materials and process. We will like designs that allow us to use UV spot varnish and other techniques that will differentiate us.

We are including Two different versions of Color logos. In addition we are including white over black background logos. Those can be used replacing the black for a color.

Please note this is the first time we will be creating any corporate materials with our new logo and colors.

Target Market(s)

34+ consumers of medium high and high socioeconomic levels.

Industry/Entity Type

Health

Requirements
Must have
• Our logo on its original colors
Should not have
• Any other graphical element or design that is not our logo

```html
<!DOCTYPE html>
<html lang="en">
<head>
<meta charset="utf-8">
<title>VELUNDA Business Card Set</title>
<link rel="stylesheet" href="https://fonts.googleapis.com/css2?family=Jost:ital,wght@0,400;0,500;0,600;1,600&display=swap">
<style>
  :root {
    --page-bg: #7a5237;
    --label: #1e1207;
    --brand-blue: #1d5a85;
    --brand-teal: #2aa08f;
    --band-line: #7cc3e6;
    --white: #ffffff;
    --ink: #1b1b1b;
    --web-grey: #4a4a4a;
    --silver-1: #f2f2f2;
    --silver-2: #c9c9c9;
    --steel-light: #e8e8e8;
    --steel-dark: #1e1e1e;
  }
  * { box-sizing: border-box; margin: 0; padding: 0; }
  html, body { width: 1200px; height: 788px; overflow: hidden; }
  body {
    position: relative;
    background: var(--page-bg);
    font-family: "Jost", "Futura", sans-serif;
  }
  .view-label {
    position: absolute;
    width: 200px;
    text-align: center;
    font-size: 20px;
    color: var(--label);
  }
  .card {
    position: absolute;
    width: 525px;
    height: 300px;
    border-radius: 20px;
    overflow: hidden;
  }
  .card--front { left: 53px; top: 75px; background: linear-gradient(180deg, var(--silver-1), var(--silver-2) 60%, #e4e4e4); }
  .card--back-white { left: 622px; top: 75px; background: var(--white); }
  .card--back-steel { left: 53px; top: 445px; background: linear-gradient(35deg, var(--steel-dark) 10%, #6d6d6d 45%, var(--steel-light) 90%); }
  .card--back-blue { left: 622px; top: 445px; background: var(--brand-blue); }

  .brand { position: absolute; display: flex; align-items: center; }
  .brand__dot { border-radius: 50%; background: var(--brand-teal); flex: none; }
  .brand__name { font-weight: 600; letter-spacing: 2px; line-height: 1; color: var(--brand-blue); }

  .card--front .brand { left: 130px; top: 65px; gap: 22px; }
  .card--front .brand__dot { width: 58px; height: 58px; }
  .card--front .brand__name { font-size: 40px; }

  .info-band {
    position: absolute; left: 0; top: 151px; width: 100%; height: 70px;
    background: var(--brand-blue);
    border-top: 2px solid var(--band-line);
    border-bottom: 2px solid var(--band-line);
    color: var(--white);
  }
  .person { position: absolute; left: 57px; top: 12px; }
  .person__name { font-size: 18px; font-weight: 600; }
  .person__role { font-size: 13px; }
  .lines { position: absolute; right: 56px; top: 14px; text-align: right; font-size: 14px; line-height: 20px; }
  .lines b { font-style: italic; font-weight: 600; }
  .contact {
    position: absolute; left: 0; top: 238px; width: 100%;
    text-align: center; font-size: 13px; line-height: 19px; color: var(--ink);
  }
  .contact b { font-style: italic; font-weight: 600; }

  .card--back-white .brand { left: 100px; top: 88px; gap: 30px; }
  .card--back-white .brand__dot { width: 70px; height: 70px; }
  .card--back-white .brand__name { font-size: 52px; }

  .card--back-steel .brand { left: 95px; top: 128px; gap: 30px; }
  .card--back-steel .brand__dot { width: 70px; height: 70px; }
  .card--back-steel .brand__name { font-size: 50px; }

  .card--back-blue .brand { left: 0; top: 40px; width: 100%; flex-direction: column; gap: 55px; }
  .card--back-blue .brand__dot { width: 72px; height: 72px; }
  .card--back-blue .brand__name { font-size: 48px; color: var(--white); }

  .web {
    position: absolute; left: 0; width: 100%; top: 258px;
    text-align: center; font-size: 16px; letter-spacing: 3px;
  }
  .card--back-white .web { color: var(--web-grey); }
  .card--back-steel .web, .card--back-blue .web { color: var(--white); }
</style>
</head>
<body>
  <div class="view-label" style="left:220px; top:34px;">Front</div>
  <div class="view-label" style="left:796px; top:34px;">Back - 1</div>
  <div class="view-label" style="left:225px; top:404px;">Back - 2</div>
  <div class="view-label" style="left:796px; top:404px;">Back - 3</div>

  <section class="card card--front">
    <div class="brand"><span class="brand__dot"></span><span class="brand__name">VELUNDA</span></div>
    <div class="info-band">
      <div class="person">
        <div class="person__name">Your Name</div>
        <div class="person__role">Designation</div>
      </div>
      <div class="lines">
        <div><b>phone</b> : +12 345 67890</div>
        <div><b>fax</b> : +12 345 67890</div>
      </div>
    </div>
    <div class="contact">
      <div><b>email</b> : info@velunda.example &nbsp;|&nbsp; <b>web</b> : www.velunda.example</div>
      <div>#0000, Street Name, Area Name, Country Code</div>
    </div>
  </section>

  <section class="card card--back-white">
    <div class="brand"><span class="brand__dot"></span><span class="brand__name">VELUNDA</span></div>
    <div class="web">www.velunda.example</div>
  </section>

  <section class="card card--back-steel">
    <div class="brand"><span class="brand__dot"></span><span class="brand__name">VELUNDA</span></div>
    <div class="web">www.velunda.example</div>
  </section>

  <section class="card card--back-blue">
    <div class="brand"><span class="brand__dot"></span><span class="brand__name">VELUNDA</span></div>
    <div class="web">www.velunda.example</div>
  </section>
</body>
</html>
```